Professional & attention grabbing.

A business card design, front and back. I already have a logo I will attach, but I am open to something new as well.
Things to include:
Name:
Title:
Phone:
Email:
Wanting something that is professional but attention grabbing.
Also we do a lot of work using drones on natural gas pipelines (leading the future)if you want to include any of that. I'm open to ideas.
Target Market(s)
Natural gas transmission industry / greenhouse gas mitigation industry
Industry/Entity Type
Business
Colors
Designer to choose colors to be used in the design.
Look and feel
Each slider illustrates characteristics of the customer's brand and the style your logo design should communicate.

```html
<!DOCTYPE html>
<html lang="en">
<head>
<meta charset="utf-8">
<title>Ridgeline Inspections – Business Card</title>
<link rel="stylesheet" href="https://fonts.googleapis.com/css2?family=Montserrat:wght@400;600;700&display=swap">
<style>
  :root {
    --brand-red: #c8202a;
    --brand-red-deep: #a8151e;
    --ink: #3a3a3c;
    --paper: #ffffff;
    --backdrop: #e8e5e0;
  }
  * { margin: 0; padding: 0; box-sizing: border-box; }
  html, body {
    width: 1200px;
    height: 950px;
    overflow: hidden;
    background: var(--backdrop);
    font-family: "Montserrat", sans-serif;
  }
  .card-set {
    position: relative;
    width: 1200px;
    height: 950px;
    display: flex;
    justify-content: center;
    align-items: center;
    gap: 70px;
  }
  .card {
    position: relative;
    width: 420px;
    height: 680px;
    border-radius: 26px;
    background: var(--paper);
    overflow: hidden;
    box-shadow: 0 10px 30px rgba(0,0,0,0.15);
  }
  .card-front .red-field {
    position: absolute;
    inset: 0;
    width: 100%;
    height: 100%;
  }
  .contact {
    position: absolute;
    left: 0;
    right: 0;
    top: 430px;
    text-align: center;
    color: var(--paper);
  }
  .contact-name {
    font-size: 26px;
    font-weight: 700;
    letter-spacing: 1.5px;
    text-transform: uppercase;
  }
  .contact-title {
    font-size: 18px;
    font-weight: 400;
    margin-top: 4px;
    margin-bottom: 22px;
  }
  .contact-list {
    list-style: none;
    display: inline-block;
    text-align: left;
  }
  .contact-list li {
    display: flex;
    align-items: center;
    gap: 10px;
    font-size: 17px;
    line-height: 1.6;
  }
  .contact-list svg { width: 16px; height: 16px; flex: none; }
  .card-back {
    display: flex;
    align-items: center;
    justify-content: center;
  }
  .brand-lockup {
    display: flex;
    align-items: center;
    gap: 16px;
  }
  .brand-dot {
    width: 22px;
    height: 22px;
    border-radius: 50%;
    background: var(--brand-red);
  }
  .brand-name {
    font-size: 34px;
    font-weight: 700;
    line-height: 1.15;
    color: var(--ink);
    text-transform: uppercase;
    letter-spacing: 1px;
  }
</style>
</head>
<body>
  <main class="card-set">
    <section class="card card-front" aria-label="Card front">
      <svg class="red-field" viewBox="0 0 420 680" preserveAspectRatio="none" aria-hidden="true">
        <path d="M0 240 C 110 330, 250 330, 330 250 C 380 200, 400 120, 420 80 L420 680 L0 680 Z" fill="var(--brand-red)"/>
      </svg>
      <div class="contact">
        <p class="contact-name">Dana Whitfield</p>
        <p class="contact-title">CEO/Founder</p>
        <ul class="contact-list">
          <li>
            <svg viewBox="0 0 16 16" aria-hidden="true"><path d="M4 1.5 6.3 4.2 5 6a8 8 0 0 0 5 5l1.8-1.3 2.7 2.3-1.5 2.2C7 14 2 9 1.8 3z" fill="currentColor"/></svg>
            555 204 7719
          </li>
          <li>
            <svg viewBox="0 0 16 16" aria-hidden="true"><rect x="1" y="3" width="14" height="10" rx="1" fill="currentColor"/><path d="M1.5 4 8 9l6.5-5" stroke="var(--brand-red)" stroke-width="1.3" fill="none"/></svg>
            dana@ridgelineinspect.com
          </li>
          <li>
            <svg viewBox="0 0 16 16" aria-hidden="true"><circle cx="8" cy="8" r="6.5" stroke="currentColor" stroke-width="1.5" fill="none"/><path d="M1.5 8h13M8 1.5c-3 3.5-3 9.5 0 13M8 1.5c3 3.5 3 9.5 0 13" stroke="currentColor" stroke-width="1.2" fill="none"/></svg>
            www.ridgelineinspect.com
          </li>
        </ul>
      </div>
    </section>

    <section class="card card-back" aria-label="Card back">
      <div class="brand-lockup">
        <span class="brand-dot" aria-hidden="true"></span>
        <p class="brand-name">Ridgeline<br>Inspections</p>
      </div>
    </section>
  </main>
</body>
</html>
```